MarbleTrove - New Website Design

Create a professional Vendora website for the hottest trend; a box of school supplies subscription box business called MarbleTrove. Vendora.com is an easy to use website builder.
Please see fizwickpod.com; plumfolly.com; tarrowmintloft.com; and nipcove.com for the concept I am after. The business has not been launched yet, I am currently in the pre-launch stage using a specialized landing page website, and so the time scale for developing my professional looking Vendora website is up to 1-2 weeks.
The webpage should have a fun feel and should match the style of the company logo at plumfolly.com. The pages to include are 'Home', 'About us' and 'Get Started'
Thank you and good luck!
1 page

```html
<!DOCTYPE html>
<html lang="en">
<head>
<meta charset="utf-8">
<title>MarbleTrove – Home</title>
<link rel="stylesheet" href="https://fonts.googleapis.com/css2?family=Montserrat:wght@400;500;600;700&family=Raleway:wght@400;500;600&display=swap">
<style>
:root{
  --pink:#f66fa6;
  --teal:#33d6b8;
  --dark:#1e1e1e;
  --darker:#0f0f0f;
  --ink:#222;
  --grey:#8a8a8a;
  --light:#f4f4f4;
  --white:#fff;
}
*{box-sizing:border-box;margin:0;padding:0}
html,body{width:1200px;height:3939px;overflow:hidden}
body{font-family:'Raleway',sans-serif;color:var(--ink);background:var(--white);position:relative}
h1,h2,h3,h4,.btn,.nav a,.logo{font-family:'Montserrat',sans-serif}
.abs{position:absolute}
.photo{position:absolute}
/* top bar */
.topbar{position:absolute;left:0;top:0;width:1200px;height:26px;background:var(--pink);color:var(--white);font-size:11px;font-family:'Montserrat',sans-serif}
.topbar .login{position:absolute;left:87px;top:7px}
.topbar .phone{position:absolute;left:305px;top:7px}
.topbar .social{position:absolute;right:87px;top:5px;display:flex;gap:6px}
.topbar .social span{width:16px;height:16px;border-radius:50%;background:var(--white)}
/* nav */
.header{position:absolute;left:0;top:26px;width:1200px;height:74px;background:var(--white)}
.logo{position:absolute;left:87px;top:22px;display:flex;align-items:center;gap:8px;font-weight:700;font-size:26px;color:var(--pink);letter-spacing:.5px}
.logo i{width:20px;height:20px;border-radius:50%;background:var(--teal);display:block}
.nav{position:absolute;left:484px;top:0;height:74px;display:flex}
.nav a{display:flex;align-items:center;justify-content:center;height:74px;font-size:13px;font-weight:500;color:var(--ink);text-decoration:none;border-left:1px solid #e6e6e6}
.nav a:last-child{border-right:1px solid #e6e6e6}
.search{position:absolute;left:1093px;top:28px}
.rainbow{position:absolute;left:0;top:96px;width:1200px;height:4px;background:linear-gradient(90deg,var(--pink),#ffd23f,var(--teal),#5aa7ff,var(--pink),#ffd23f,var(--teal))}
/* hero */
.hero-photo{left:0;top:100px;width:1200px;height:596px;background:linear-gradient(120deg,#d9c9b3,#9fb7c9 35%,#e7d6c1 60%,#6fae7d 85%,#c48c58)}
.hero-box{position:absolute;left:262px;top:257px;width:683px;height:281px;background:rgba(255,255,255,.35);text-align:center}
.hero-box h1{margin-top:40px;font-size:34px;font-weight:600;color:var(--ink)}
.rule{display:block;margin:10px auto 0}
.hero-box p{font-size:17px;line-height:27px;color:var(--ink);margin:12px auto 0;width:560px}
.btns{display:flex;justify-content:center;gap:22px;margin-top:22px}
.btn{display:inline-flex;align-items:center;justify-content:center;height:54px;border-radius:27px;color:var(--white);font-size:15px;font-weight:500;letter-spacing:.3px}
.btn.teal{background:var(--teal);width:190px}
.btn.pink{background:var(--pink);width:190px}
/* welcome */
.welcome h3{position:absolute;left:87px;top:775px;font-size:22px;font-weight:600}
.welcome h2{position:absolute;left:87px;top:810px;font-size:38px;font-weight:400;letter-spacing:2px;color:#333}
.welcome .rule-l{position:absolute;left:87px;top:867px}
.welcome p{position:absolute;left:87px;top:908px;width:590px;font-size:14.5px;line-height:24px;color:var(--grey)}
.welcome .btn{position:absolute;left:87px;top:1118px;width:188px}
.kids-photo{left:683px;top:762px;width:472px;height:485px;background:linear-gradient(160deg,#ffffff 0%,#f3c24a 30%,#e88a3a 55%,#4d7fb5 80%,#ffffff 100%)}
/* how it works */
.how{position:absolute;left:0;top:1274px;width:1200px;height:467px;background:linear-gradient(180deg,#1d1a17,#2a2622 50%,#1a1714)}
.how h2{position:absolute;top:40px;width:100%;text-align:center;color:var(--white);font-size:36px;font-weight:500}
.how .rule-c{position:absolute;left:560px;top:90px}
.step{position:absolute;top:140px;width:320px;text-align:center;color:var(--white)}
.step .ring{width:130px;height:130px;margin:0 auto;border-radius:50%;border:3px solid;display:flex;align-items:center;justify-content:center}
.step .dot{width:110px;height:110px;border-radius:50%;display:flex;align-items:center;justify-content:center}
.step h4{margin-top:22px;font-size:21px;font-weight:600}
.step p{margin-top:16px;font-size:13.5px;line-height:22px;color:#e6e6e6}
.arrow{position:absolute;top:190px}
/* packages */
.sec-title{position:absolute;width:1200px;text-align:center;font-size:38px;font-weight:600;color:var(--ink)}
.sec-sub{position:absolute;width:1200px;text-align:center;font-size:13.5px;line-height:24px;color:var(--grey)}
.card{position:absolute;top:2001px;width:327px;height:376px;background:var(--light)}
.card .pic{position:absolute;left:0;top:0;width:327px;height:165px;background:linear-gradient(135deg,#6b8fbf,#e8c35b 40%,#d9574c 65%,#d6d1c4)}
.card .price{position:absolute;right:0;top:0;width:70px;height:52px;background:var(--pink);color:var(--white);font-family:'Montserrat',sans-serif;font-size:28px;font-weight:600;display:flex;align-items:center;justify-content:center}
.card .tag{position:absolute;left:0;top:130px;width:130px;height:35px;background:linear-gradient(90deg,var(--teal),rgba(51,214,184,0));color:var(--white);font-family:'Montserrat',sans-serif;font-size:18px;font-weight:600;padding:7px 0 0 14px}
.card ul{position:absolute;left:50px;top:198px;list-style:none}
.card li{font-size:14px;height:36px;position:relative;padding-left:26px}
.card li::before{content:"»";position:absolute;left:0;top:-4px;color:var(--pink);font-size:20px}
.card .choose{position:absolute;right:0;bottom:0;width:122px;height:46px;background:var(--pink);color:var(--white);font-family:'Montserrat',sans-serif;font-size:20px;font-weight:500;display:flex;align-items:center;justify-content:center}
/* inside */
.desk-photo{left:0;top:2450px;width:530px;height:447px;background:linear-gradient(135deg,#a46a3f,#c98d5a 50%,#8c5631)}
.inside{position:absolute;left:530px;top:2450px;width:670px;height:447px;background:var(--teal);color:var(--white)}
.inside h3{position:absolute;left:50px;top:56px;font-size:22px;font-weight:600;color:var(--ink)}
.inside h2{position:absolute;left:50px;top:88px;font-size:27px;font-weight:400;letter-spacing:1.5px;color:var(--ink)}
.inside .rule-l{position:absolute;left:50px;top:144px}
.inside p{position:absolute;left:50px;top:186px;width:590px;font-size:14.5px;line-height:24px}
.inside .btn{position:absolute;left:50px;top:342px;width:190px;height:54px;background:var(--pink);font-size:13px}
/* gallery */
.g{position:absolute}
/* footer */
.footer{position:absolute;left:0;top:3558px;width:1200px;height:323px;background:var(--dark);color:var(--white)}
.footer .logo{left:100px;top:80px;color:var(--pink)}
.f-info{position:absolute;left:90px;top:160px;font-size:13px;line-height:20px}
.f-info div{display:flex;gap:12px;margin-bottom:18px;align-items:flex-start}
.f-col{position:absolute;top:60px}
.f-col h4{font-size:14px;font-weight:500;margin-bottom:26px}
.f-col li{list-style:none;font-size:13px;height:32px;display:flex;align-items:center;gap:14px}
.f-col li::before{content:"→";color:var(--white)}
.f-form{position:absolute;left:874px;top:60px}
.f-form h4{font-size:14px;font-weight:500;margin-bottom:22px}
.f-form .field{width:202px;height:28px;border:1px solid #cfcfcf;margin-bottom:12px;font-size:10px;color:#bbb;padding:8px 6px}
.f-form .submit{width:202px;height:28px;background:var(--teal);font-family:'Montserrat',sans-serif;font-size:14px;font-weight:600;display:flex;align-items:center;justify-content:center}
.copy{position:absolute;left:0;top:3881px;width:1200px;height:58px;background:var(--darker);color:#ccc;font-size:11px;text-align:center;padding-top:22px}
</style>
</head>
<body>

<div class="topbar">
  <div class="login">&#10148;&nbsp; LOGIN &nbsp;/&nbsp; REGISTER</div>
  <div class="phone">&#9990;&nbsp; +00 11 222 333 4444</div>
  <div class="social"><span></span><span></span><span></span></div>
</div>

<header class="header">
  <div class="logo"><i></i>MARBLETROVE</div>
  <nav class="nav">
    <a style="width:107px">HOME</a>
    <a style="width:155px">ABOUT US</a>
    <a style="width:185px">GET STARTED</a>
    <a style="width:152px">CONTACTS</a>
  </nav>
  <svg class="search" width="18" height="18" viewBox="0 0 18 18"><circle cx="7.5" cy="7.5" r="5.5" fill="none" stroke="#999" stroke-width="1.6"/><line x1="11.5" y1="11.5" x2="16" y2="16" stroke="#999" stroke-width="1.6"/></svg>
</header>
<div class="rainbow"></div>

<section>
  <div class="photo hero-photo" role="img" aria-label="Children drawing together at a classroom table"></div>
  <div class="hero-box">
    <h1>LOREM IPSUM IS SIMPLY DUMMY</h1>
    <svg class="rule" width="90" height="6"><line x1="0" y1="3" x2="90" y2="3" stroke="#33d6b8" stroke-width="2"/></svg>
    <p>It is a long established fact that a reader will be distracted by the readable content of a page when looking at its layout.</p>
    <div class="btns"><span class="btn teal">GET STARTED</span><span class="btn pink">GIVE A GIFT</span></div>
  </div>
</section>

<section class="welcome">
  <h3>WELCOME TO</h3>
  <h2>MARBLETROVE</h2>
  <svg class="rule-l" width="110" height="8"><line x1="0" y1="4" x2="110" y2="4" stroke="#f66fa6" stroke-width="1.5"/><rect x="90" y="1" width="6" height="6" fill="#f66fa6"/></svg>
  <p>Lorem Ipsum is simply dummy text of the printing and typesetting industry. Lorem Ipsum has been the industry's standard dummy text ever since the 1500s, when an unknown printer took a galley of type and scrambled it to make a type specimen book. It has survived not only five centuries, but also the leap into electronic typesetting, remaining essentially unchanged. It was popularised in the 1960s with the release of Letraset sheets containing Lorem Ipsum passages, and more recently with desktop publishing software like Aldus PageMaker including versions of Lorem Ipsum.</p>
  <span class="btn pink">GET STARTED</span>
  <div class="photo kids-photo" role="img" aria-label="Group of cheerful school children sitting together"></div>
</section>

<section class="how">
  <h2>HOW IT WORKS</h2>
  <svg class="rule-c" width="80" height="8"><line x1="0" y1="4" x2="80" y2="4" stroke="#f66fa6" stroke-width="1.5"/><rect x="37" y="1" width="6" height="6" fill="#f66fa6"/></svg>
  <div class="step" style="left:90px">
    <div class="ring" style="border-color:var(--pink)"><div class="dot" style="background:var(--pink)">
      <svg width="44" height="40" viewBox="0 0 44 40" fill="none" stroke="#fff" stroke-width="2.5"><rect x="3" y="3" width="38" height="10"/><rect x="6" y="13" width="32" height="24"/><line x1="16" y1="21" x2="28" y2="21"/></svg>
    </div></div>
    <h4>LOREM IPSUM</h4>
    <p>It is a long established fact that a reader will be distracted by the readable content of a page when looking at its layout.</p>
  </div>
  <svg class="arrow" style="left:410px" width="26" height="44"><polygon points="0,0 26,22 0,44" fill="#6a6a6a"/></svg>
  <div class="step" style="left:441px">
    <div class="ring" style="border-color:#888"><div class="dot" style="background:#777">
      <svg width="44" height="40" viewBox="0 0 44 40" fill="none" stroke="#fff" stroke-width="2.5"><rect x="3" y="3" width="38" height="10"/><rect x="6" y="13" width="32" height="24"/><line x1="16" y1="21" x2="28" y2="21"/></svg>
    </div></div>
    <h4>LOREM IPSUM</h4>
    <p>It is a long established fact that a reader will be distracted by the readable content of a page when looking at its layout.</p>
  </div>
  <svg class="arrow" style="left:762px" width="26" height="44"><polygon points="0,0 26,22 0,44" fill="#6a6a6a"/></svg>
  <div class="step" style="left:791px">
    <div class="ring" style="border-color:var(--teal)"><div class="dot" style="background:var(--teal)">
      <svg width="44" height="40" viewBox="0 0 44 40" fill="none" stroke="#fff" stroke-width="2.5"><rect x="3" y="3" width="38" height="10"/><rect x="6" y="13" width="32" height="24"/><line x1="16" y1="21" x2="28" y2="21"/></svg>
    </div></div>
    <h4>LOREM IPSUM</h4>
    <p>It is a long established fact that a reader will be distracted by the readable content of a page when looking at its layout.</p>
  </div>
</section>

<section class="packages">
  <h2 class="sec-title" style="top:1810px">CHOOSE A PACKAGE</h2>
  <p class="sec-sub" style="top:1876px">There are many variations of passages of Lorem Ipsum available, but the majority have suffered alteration in some form.<br>There are many variations of passages of Lorem Ipsum available</p>
  <svg class="abs" style="left:560px;top:1950px" width="80" height="8"><line x1="0" y1="4" x2="80" y2="4" stroke="#f66fa6" stroke-width="1.5"/><rect x="37" y="1" width="6" height="6" fill="#f66fa6"/></svg>

  <div class="card" style="left:87px">
    <div class="pic" role="img" aria-label="Notebooks and colored pencils"></div>
    <div class="price">$15</div><div class="tag">Minimal</div>
    <ul><li>Lorem Ipsum is not simply</li><li>Lorem Ipsum is not simply</li><li>Lorem Ipsum is not simply</li><li>Lorem Ipsum is not simply</li></ul>
    <div class="choose">Choose</div>
  </div>
  <div class="card" style="left:436px">
    <div class="pic" role="img" aria-label="Notebooks and colored pencils"></div>
    <div class="price">$15</div><div class="tag">Standerd</div>
    <ul><li>Lorem Ipsum is not simply</li><li>Lorem Ipsum is not simply</li><li>Lorem Ipsum is not simply</li><li>Lorem Ipsum is not simply</li></ul>
    <div class="choose">Choose</div>
  </div>
  <div class="card" style="left:786px">
    <div class="pic" role="img" aria-label="Notebooks and colored pencils"></div>
    <div class="price">$15</div><div class="tag">Ultimate</div>
    <ul><li>Lorem Ipsum is not simply</li><li>Lorem Ipsum is not simply</li><li>Lorem Ipsum is not simply</li><li>Lorem Ipsum is not simply</li></ul>
    <div class="choose">Choose</div>
  </div>
</section>

<section>
  <div class="photo desk-photo" role="img" aria-label="School supplies and a tablet on a wooden desk"></div>
  <div class="inside">
    <h3>WHAT'S INSIDE</h3>
    <h2>A THEMED COLLECTION EVERY MONTH</h2>
    <svg class="rule-l" width="110" height="8"><line x1="0" y1="4" x2="110" y2="4" stroke="#f66fa6" stroke-width="1.5"/><rect x="100" y="1" width="6" height="6" fill="#f66fa6"/></svg>
    <p>Lorem Ipsum is simply dummy text of the printing and typesetting industry. Lorem Ipsum has been the industry's standard dummy text ever since the 1500s, when an unknown printer took a galley of type and scrambled it to make a type specimen book. It has survived not only five centuries, but also the leap into electronic typesetting.</p>
    <span class="btn">FETCH YOURS NOW</span>
  </div>
</section>

<section class="gallery">
  <h2 class="sec-title" style="top:2960px">OUR GALLERY</h2>
  <p class="sec-sub" style="top:3024px">There are many variations of passages of Lorem Ipsum available, but the majority have suffered alteration in some form.<br>There are many variations of passages of Lorem Ipsum available</p>
  <svg class="abs" style="left:560px;top:3092px" width="80" height="8"><line x1="0" y1="4" x2="80" y2="4" stroke="#f66fa6" stroke-width="1.5"/><rect x="37" y="1" width="6" height="6" fill="#f66fa6"/></svg>
  <div class="g" style="left:87px;top:3133px;width:325px;height:352px;background:linear-gradient(135deg,#4fb8e0,#2a8fc4 50%,#f2c94c)" role="img" aria-label="Open blue supply organizer filled with crayons"></div>
  <div class="g" style="left:436px;top:3133px;width:326px;height:165px;background:linear-gradient(135deg,#3b5b9c,#d9d2e0 50%,#e77fa4)" role="img" aria-label="Colorful school bags"></div>
  <div class="g" style="left:436px;top:3322px;width:326px;height:163px;background:linear-gradient(135deg,#e9a3b8,#f4e2c7 50%,#7fcfc0)" role="img" aria-label="Back to school gift bags"></div>
  <div class="g" style="left:786px;top:3133px;width:327px;height:165px;background:linear-gradient(135deg,#7c6b5e,#e24a3b 45%,#f3e04a)" role="img" aria-label="Pile of markers and stationery"></div>
  <div class="g" style="left:786px;top:3322px;width:327px;height:163px;background:linear-gradient(135deg,#f5d72f,#f1c40f 60%,#9ba7b5)" role="img" aria-label="Yellow pencil cases"></div>
</section>

<footer class="footer">
  <div class="logo"><i></i>MARBLETROVE</div>
  <div class="f-info">
    <div><svg width="12" height="16" viewBox="0 0 12 16"><path d="M6 0a6 6 0 0 1 6 6c0 4-6 10-6 10S0 10 0 6a6 6 0 0 1 6-6z" fill="#33d6b8"/><circle cx="6" cy="6" r="2" fill="#1e1e1e"/></svg><span>14 Alder Row, Brookfield, ZZ 00000<br>Hours: 9:00am - 5:00pm CST</span></div>
    <div><svg width="14" height="14" viewBox="0 0 14 14"><path d="M3 0l3 3-2 2c1 2 3 4 5 5l2-2 3 3-2 3C6 14 0 8 0 3z" fill="#33d6b8"/></svg><b>(555) 014-2290</b></div>
    <div><svg width="16" height="12" viewBox="0 0 16 12"><rect width="16" height="12" rx="1" fill="#33d6b8"/><path d="M0 1l8 6 8-6" fill="none" stroke="#1e1e1e" stroke-width="1.2"/></svg><span>marbletrove.com</span></div>
  </div>
  <div class="f-col" style="left:416px"><h4>Quick Links</h4><ul><li>Home</li><li>About us</li><li>Get Started</li><li>Pricing</li><li>Contact us</li></ul></div>
  <div class="f-col" style="left:636px"><h4>Package</h4><ul><li>Lorem lossum</li><li>Lorem lossum</li><li>Lorem lossum</li><li>Lorem lossum</li></ul></div>
  <div class="f-form"><h4>Contact Us</h4><div class="field">Name...</div><div class="field">Email...</div><div class="field">Phone No...</div><div class="submit">SUBMIT</div></div>
</footer>
<div class="copy">marbletrove.com 2017. All rights reserved</div>

</body>
</html>
```